Business card for my new company (Accounting firm)

I need a business card for my new business Brightwell Advisory and Ledger SA. Our services are accounting, tax, audit and financial management. Our customers are small companies, start-ups and new companies. The final design has to show financial security, trust and growth. Please find our logo attached to the business card. Text for the business card: Brightwell Advisory and Ledger SA Tomas Varenholt Director and Founder Certified Accountant Tel. 022 418 57 34 tv@clairevalconseil.ch www.clairevalconseil.ch Rue des Vergières 27 1201 Geneva
Target Market(s)
Our customers are small companies, start-ups and new companies.
Industry/Entity Type
Finance And Accounting
Contact Information for Business Card
Claireval Conseil et Comptes SA
Tomas Varenholt
Directeur et Fondateur
Expert-comptable diplômé
Tél. 022 418 57 34
tv@clairevalconseil.ch
www.clairevalconseil.ch
Rue des Vergières 27
1201 Genève

```html
<!DOCTYPE html>
<html lang="fr">
<head>
<meta charset="utf-8">
<title>Claireval Conseil et Comptes SA – Carte de visite</title>
<link rel="stylesheet" href="https://fonts.googleapis.com/css2?family=Roboto:wght@300;400;500;700&display=swap">
<style>
  :root {
    --stage: #e4e5e7;
    --blue-light: #2ea3d6;
    --blue-mid: #1f82b8;
    --blue-deep: #1a5f8f;
    --name-blue: #1d5f93;
    --ink: #3a3b3d;
    --ink-soft: #55575a;
    --charcoal: #2f3033;
    --paper: #f4f4f4;
    --white: #ffffff;
  }
  * { box-sizing: border-box; margin: 0; padding: 0; }
  html, body {
    width: 1200px; height: 726px; overflow: hidden;
    background: var(--stage);
    font-family: "Roboto", Arial, sans-serif;
  }
  .stage {
    position: relative; width: 1200px; height: 726px;
    display: flex; align-items: center; justify-content: center; gap: 48px;
  }
  .card {
    position: relative; width: 520px; height: 312px; overflow: hidden;
    border-radius: 3px;
    box-shadow: 0 10px 24px rgba(0,0,0,0.14), 0 2px 4px rgba(0,0,0,0.08);
  }

  /* Front */
  .card-front {
    background: linear-gradient(160deg, var(--blue-light) 0%, var(--blue-mid) 55%, var(--blue-deep) 100%);
    color: var(--white);
    display: flex; flex-direction: column; align-items: center; justify-content: center;
  }
  .front-brand {
    font-weight: 500; font-size: 34px; letter-spacing: 3px; text-transform: uppercase;
  }
  .front-web {
    position: absolute; bottom: 34px; left: 0; right: 0; text-align: center;
    font-weight: 500; font-size: 15px; letter-spacing: 0.3px;
  }

  /* Back */
  .card-back { background: var(--paper); color: var(--ink); }
  .brand {
    position: absolute; left: 40px; top: 48px;
    display: flex; align-items: center; gap: 14px;
  }
  .brand-square { width: 40px; height: 40px; background: var(--blue-mid); flex: none; }
  .brand-name {
    font-weight: 500; font-size: 24px; color: var(--ink); letter-spacing: 0.5px; white-space: nowrap;
  }
  .person { position: absolute; left: 40px; top: 176px; }
  .person-name { font-weight: 700; font-size: 22px; color: var(--name-blue); margin-bottom: 6px; white-space: nowrap; }
  .person-role { font-size: 13px; color: var(--ink-soft); line-height: 1.4; white-space: nowrap; }

  .contact {
    position: absolute; right: 36px; top: 128px;
    list-style: none; font-size: 13.5px; color: var(--ink);
  }
  .contact li { display: flex; align-items: center; gap: 10px; line-height: 22px; white-space: nowrap; }
  .contact svg { width: 13px; height: 13px; fill: var(--ink-soft); flex: none; }

  .address-band {
    position: absolute; right: 0; bottom: 0; width: 280px; height: 56px; z-index: 2;
    background: linear-gradient(90deg, var(--blue-deep), var(--blue-light));
    border-top-left-radius: 22px;
    color: var(--white); font-size: 13.5px; white-space: nowrap;
    display: flex; align-items: center; justify-content: center;
  }
  .base-strip {
    position: absolute; left: 0; right: 0; bottom: 0; height: 16px; z-index: 1;
    background: var(--charcoal);
  }
</style>
</head>
<body>
<main class="stage">
  <section class="card card-front" aria-label="Recto">
    <p class="front-brand">Claireval</p>
    <p class="front-web">www.clairevalconseil.ch</p>
  </section>

  <section class="card card-back" aria-label="Verso">
    <div class="brand">
      <span class="brand-square"></span>
      <span class="brand-name">Claireval Conseil et Comptes</span>
    </div>

    <div class="person">
      <p class="person-name">Tomas Varenholt</p>
      <p class="person-role">Directeur et Fondateur<br>Expert-comptable diplômé</p>
    </div>

    <ul class="contact">
      <li>
        <svg viewBox="0 0 16 16" aria-hidden="true"><path d="M3 1h3l1.5 4-2 1.3a9 9 0 0 0 4.2 4.2L11 8.5l4 1.5v3a2 2 0 0 1-2 2A12 12 0 0 1 1 3a2 2 0 0 1 2-2z"/></svg>
        022 418 57 34
      </li>
      <li>
        <svg viewBox="0 0 16 16" aria-hidden="true"><path d="M1 3h14v10H1z M1 3l7 6 7-6" fill="none" stroke="#55575a" stroke-width="1.6"/></svg>
        tv@clairevalconseil.ch
      </li>
      <li>
        <svg viewBox="0 0 16 16" aria-hidden="true"><circle cx="8" cy="8" r="6.5" fill="none" stroke="#55575a" stroke-width="1.4"/><path d="M1.5 8h13M8 1.5c-3 3.5-3 9.5 0 13M8 1.5c3 3.5 3 9.5 0 13" fill="none" stroke="#55575a" stroke-width="1.2"/></svg>
        www.clairevalconseil.ch
      </li>
    </ul>

    <div class="address-band">Rue des Vergières 27 1201 Genève</div>
    <div class="base-strip"></div>
  </section>
</main>
</body>
</html>
```